Redesign of business card for Cedar Ridge Mechanical

We are looking for a new design for our business cards for Cedar Ridge Mechanical. We are a plumbing & HVAC construction company, operating on the West Coast of Canada and USA. Logo attached.
Industry/Entity Type
Construction - Plumbing & HVAC
Contact Information for Business Card
Name, address, phone numbers, email, website address
Look and feel
Each slider illustrates characteristics of the customer's brand and the style your logo design should communicate.

```html
<!DOCTYPE html>
<html lang="en">
<head>
<meta charset="UTF-8">
<title>Cedar Ridge Mechanical – Business Card</title>
<link href="https://fonts.googleapis.com/css2?family=Montserrat:wght@400;500;700&display=swap" rel="stylesheet">
<style>
  :root {
    --backdrop: #262626;
    --card-white: #ffffff;
    --card-black: #161616;
    --ink: #111111;
    --ink-soft: #8a8a8a;
    --ink-muted: #6f6f6f;
    --rule: #1a1a1a;
    --pattern-light: #232323;
    --pattern-dark: #141414;
  }
  * { box-sizing: border-box; margin: 0; padding: 0; }
  html, body {
    width: 1200px; height: 801px; overflow: hidden;
    background: var(--backdrop);
    font-family: "Montserrat", Arial, sans-serif;
  }
  .canvas {
    position: relative; width: 1200px; height: 801px;
    display: flex; align-items: center; justify-content: center; gap: 60px;
  }
  .card {
    position: relative; width: 520px; height: 297px;
    border-radius: 22px; overflow: hidden;
    box-shadow: 0 18px 40px rgba(0,0,0,.45);
  }

  /* Front side */
  .card-front { background: var(--card-white); color: var(--ink); }
  .card-front .frame { position: absolute; inset: 0; }
  .identity {
    position: absolute; left: 0; top: 112px; width: 238px;
    text-align: right;
  }
  .identity .name {
    font-weight: 700; font-size: 19px; letter-spacing: .5px;
  }
  .identity .name .surname { color: var(--ink-soft); }
  .identity .role { font-size: 13px; font-weight: 500; margin-top: 2px; }
  .divider {
    position: absolute; left: 254px; top: 106px; width: 1px; height: 60px;
    background: var(--ink-muted);
  }
  .contacts {
    position: absolute; left: 268px; top: 104px;
    list-style: none; font-size: 13.5px; color: var(--ink-muted);
  }
  .contacts li { display: flex; align-items: center; gap: 7px; height: 21px; white-space: nowrap; }
  .contacts svg { width: 12px; height: 12px; fill: var(--ink); flex: none; }
  .address {
    position: absolute; left: 0; right: 0; bottom: 22px;
    text-align: center; font-size: 13px; color: var(--ink-muted); letter-spacing: .3px;
  }

  /* Back side */
  .card-back { background: var(--card-black); }
  .monogram-pattern {
    position: absolute; inset: 0;
    background: linear-gradient(135deg, var(--pattern-light), var(--pattern-dark));
  }
  .brand {
    position: absolute; inset: 0;
    display: flex; align-items: center; justify-content: center; gap: 14px;
  }
  .brand .mark {
    width: 22px; height: 22px; background: var(--card-white);
  }
  .brand .brand-name {
    color: var(--card-white); font-weight: 700; font-size: 24px; letter-spacing: 2px;
    text-transform: uppercase;
  }
</style>
</head>
<body>
<main class="canvas">

  <section class="card card-front" aria-label="Business card front">
    <svg class="frame" width="520" height="297" viewBox="0 0 520 297" aria-hidden="true">
      <rect x="14" y="14" width="492" height="269" rx="14" fill="none" stroke="var(--rule)" stroke-width="3"/>
      <rect x="300" y="8" width="14" height="12" fill="var(--card-white)"/>
      <rect x="206" y="277" width="14" height="12" fill="var(--card-white)"/>
    </svg>

    <div class="identity">
      <p class="name">DANIEL <span class="surname">BROOKS</span></p>
      <p class="role">Manager</p>
    </div>
    <span class="divider"></span>
    <ul class="contacts">
      <li><svg viewBox="0 0 24 24"><path d="M6.6 10.8a15 15 0 0 0 6.6 6.6l2.2-2.2a1 1 0 0 1 1-.25 11.4 11.4 0 0 0 3.6.57 1 1 0 0 1 1 1V20a1 1 0 0 1-1 1A17 17 0 0 1 3 4a1 1 0 0 1 1-1h3.5a1 1 0 0 1 1 1c0 1.25.2 2.45.57 3.57a1 1 0 0 1-.25 1z"/></svg>604-555-0187</li>
      <li><svg viewBox="0 0 24 24"><path d="M2 5h20v14H2zm2 2v.5l8 5 8-5V7l-8 5z"/></svg>info@cedarridgemech.com</li>
      <li><svg viewBox="0 0 24 24"><circle cx="12" cy="12" r="10"/></svg>www.cedarridgemech.com</li>
    </ul>
    <p class="address">1480 Harbour Way, Vancouver, BC V6B 1A1</p>
  </section>

  <section class="card card-back" aria-label="Business card back">
    <div class="monogram-pattern" role="img" aria-label="Faint repeating company monogram pattern across the card"></div>
    <div class="brand">
      <span class="mark"></span>
      <span class="brand-name">Cedar Ridge Mechanical</span>
    </div>
  </section>

</main>
</body>
</html>
```